SaaS / Consulting / Solution website redesign

We need a website design that:
- Is completely different than our current design : https://plumvessel.net
- Has a very minimal amount of copy
- Changes our positioning from a SaaS application to a solutions company. Solutions company means that we help our customers solve their problems with consulting, training, and tools. An example of a solutions company is here: https://oldpages.example/web/20130111103320/http://www.brindlework.com:80/
- Does not make us look like a start up
- Is more people oriented than technology oriented

We need a designer that:
- Is a rebel at heart
- Is a minimalist
- Tells us why our current site sucks
- Can disagree with us
- Can also do copywriting or already has a copywriter that can help
- Is ok with saying we have capability that we don't in order to see if people actually want that
- Can understand the difference between our grand vision and where we need to focus ourselves today in order to get there

Who we are:
- Entrepreneurs
- Programmers
- Consultants
- Investors

Here's our design goals:
#1 Get customers, investors, employers, and partners excited about our unique and clearly articulated value proposition
#2 Get people to contact us asking for help with their programs
#3 Position ourselves as an expert in the skills based volunteering, mentorship, and group collaboration
#4 Make it easy for people, who already know who we are, to register online

What our grand vision is:
- Create a marketplace where any person can go to our site and find time with anyone they need to meet with. Whether that is their hair stylist, school advisor, parent of your kids class, dentist, attorney, etc.

What will you get if you win:
- In addition to the prize of this project we will have many landing pages and other revisions we will need in the future. We currently don't have a designer or copywriter and need to add that capability to our team

Who do we need to appeal to:
- Directors that are launching innovative programs inside organizations
- IT personnel who are trying to disqualify our technology so they don't have to support it or deal with it when it doesn't go well
- Enterprise IT architects who don't want our product being on its own island within their organization totally incompatible with everything else. Architects which are trying to assess how our platform will co-exist with all their other platforms
- Vice Presidents who want to help their directors understand that we don't have enough experience to help them
- Program managers who have to juggle a million things and need a tool that actually helps instead of confuses them and adds more work for them.
- Program managers & directors that have been given ambiguous goals by their board of directors like "improve retention, increase engagement, create innovation, get people to collaborate." And who have no idea where to start or how to deliver on things like that.
- Program managers, directors, and vice presidents that are trying to understand how our technology and services fit into their existing technology and capability
- Employees who are bored and uninspired with their current tools and are hoping for some excitement in their life. Kind of like candy or a double espresso.
- Investors who think, our company like all the rest, are going to waste their money and make them look like a fool

Other information:
-The CSS and html needs to be responsive

-Our registration onboarding flow needs to collect this information:
User first name
user last name
user email
(verify their email)
user phone number
(verify their phone number)
User profile image (optional)
User profile summary (optional, like a bio, freeform text fiels)
If applicable: Register their organization
Organization name
Organization image (optional)
Account Mailing address
account Billing address (could be same as mailing address)
account Billing email address (could be same as user address)
account Product selection (pricing tier)
account Credit card information

The designs I am getting are a good start but they are only the front page. I just want you to know that I am expecting and need more than a landing page to complete the design. I will likely need a page that outlines the benefits and features of the product itself, how its different than our competitors, which will not be on the front page. I will need a registration flow. I will need a blog page design so we can post blog articles, I will need a team page, a page that goes into detail on our training, our services. I will likely need a page that shows all news and media we have been in. I need to show customer and user quotes, case studies, a way to contact us, partners, general resources like on collaboration, product tutorials, customers. I need the site to address a comprehensive set of needs. I need that design to be consistent and thorough. I know what PlateHarbor is. I'm not using because I need more than a template that was customized. I need to be unique and match our brand thoughtfully, beautifully, and artistically. Someone asked me a question about how Murmly is similar to our tool in the way it is referred by end users and purchased by managers. Our website needs to primarily talk to the managers as I explained in the brief but it needs to appear cool and exciting to our end-users without focusing on the technology too much. Murmly is a tool that teams use to collaborate in small and large enterprises. The value prop for them is that communication is easier. But they don't put that on their website. Why? Because the users of the technology won't go to the website to find out information on it, they get their information from someone who is using it and demos it to them. When Ines tells her manager Otto "Lets get murmly, Ruth is using it at her company and its great" Ines's manager doesn't know anything about murmly so she promptly googles it. The most important thing from Ines's perspective is that Otto agrees to try it out. Otto's biggest concern is that productivity will be enhanced to degraded. Murmly knows this and so on the front page they know they are talking to Otto NOT Ines because Ines is already sold on it and doesn't need to get sold on the website. Ines is end user. Otto is the purchaser. We have the same problem and so our end users are not the ones purchasing our product, their managers are purchasing our product. We get referred by our end users and vetted by their managers. Hope this helps! Thank you for looking at this project!  Added Wednesday, June 7, 2017

Another observation I am having about the designs being submitted. I believe we used the animations on our current website because animations / cartoons connect with the "inner child" in our users. Whatever that means :-). I think it's what makes our brand fun. I have a hard time imagining that we could make the design fun looking without animations but I'm sure it can be achieved. I also recognize that blending pictures of real people and animations is hard. So either we must masterfully blend them, use only animations, or make the real people have a LOT of fun! So far most of the designs while achieve the goal of appealing to the serious Vice Presidents and directors, they are not doing a good job at appealing to the overworked program managers and bored employees. There seems to stand another challenge with animations which is animations are hard to find and/or create that achieve the message / emotion we are trying to communicate. I don't have any good answers for this but I will say we can hire both animators and illustrators if we need to. All you have to do is communicate the effect in the website design with some simpler version maybe not the end illustration or animation itself. Added Wednesday, June 7, 2017

• Sex appeal and a sense of humor. Copy that makes people excited and clairvoyant about our potential.
• Boring renditions of other non-inspiring websites

```html
<!DOCTYPE html>
<html lang="en">
<head>
<meta charset="utf-8">
<title>Clockwell — Contact Us</title>
<link rel="stylesheet" href="https://fonts.googleapis.com/css2?family=Roboto:wght@300;400;500&display=swap">
<style>
  :root {
    --brand-blue: #3db3e4;
    --action-blue: #14a3f1;
    --brand-green: #7cc576;
    --login-green: #8bc87f;
    --ink: #222629;
    --muted: #6a6f74;
    --rule: #d6d9dd;
    --field-border: #cfd3d7;
    --footer-bg: #eef0f4;
    --white: #ffffff;
  }
  * { box-sizing: border-box; margin: 0; padding: 0; }
  html, body { width: 1125px; height: 1200px; overflow: hidden; }
  body { position: relative; background: var(--white); font-family: "Roboto", Arial, sans-serif; color: var(--ink); }
  .abs { position: absolute; }

  /* Header */
  .site-header { position: absolute; left: 0; top: 0; width: 1125px; height: 100px; }
  .brand { position: absolute; display: flex; align-items: center; gap: 8px; }
  .brand-mark { width: 30px; height: 30px; border: 3px solid var(--brand-green); border-radius: 50%; }
  .brand-name { font-size: 22px; font-weight: 500; color: var(--brand-green); }
  .header-brand { left: 106px; top: 38px; }
  .main-nav a { position: absolute; top: 55px; font-size: 10px; font-weight: 500; color: #8a8f94; text-decoration: none; letter-spacing: .3px; }
  .main-nav a.is-current { color: var(--action-blue); }
  .btn-login, .btn-register { position: absolute; top: 46px; height: 31px; display: flex; align-items: center; justify-content: center; font-size: 11px; font-weight: 500; color: var(--white); text-decoration: none; }
  .btn-login { left: 845px; width: 71px; background: var(--login-green); box-shadow: 0 2px 3px rgba(0,0,0,.2); }
  .btn-register { left: 923px; width: 101px; background: var(--action-blue); box-shadow: 0 2px 3px rgba(0,0,0,.2); }

  /* Hero */
  .page-hero { position: absolute; left: 0; top: 100px; width: 1125px; height: 170px; background: var(--brand-blue); overflow: hidden; }
  .hero-title { position: absolute; left: 221px; top: 68px; font-size: 46px; font-weight: 300; color: var(--white); letter-spacing: .5px; line-height: 56px; }
  .hero-icon { position: absolute; left: 158px; top: 70px; }

  /* Breadcrumb bar */
  .breadcrumb { position: absolute; left: 103px; top: 291px; font-size: 11px; color: var(--ink); }
  .breadcrumb span { color: var(--brand-blue); }
  .site-search { position: absolute; left: 813px; top: 281px; width: 182px; height: 31px; border: 1px solid var(--field-border); padding: 0 8px; display: flex; align-items: center; font-size: 13px; color: #333; }
  .search-icon { position: absolute; left: 1000px; top: 290px; }
  .bar-rule { position: absolute; left: 103px; top: 322px; width: 918px; height: 1px; background: var(--rule); }

  /* Consultation */
  .section-title { position: absolute; left: 0; top: 374px; width: 1125px; text-align: center; font-size: 28px; font-weight: 300; letter-spacing: .4px; }
  .consult-form .field { position: absolute; left: 103px; width: 334px; height: 41px; border: 1px solid var(--field-border); padding-left: 14px; display: flex; align-items: center; font-size: 11px; color: #333; }
  .btn-submit { position: absolute; left: 103px; top: 766px; width: 182px; height: 46px; background: var(--brand-blue); color: var(--white); font-size: 15px; font-weight: 400; display: flex; align-items: center; justify-content: center; border-radius: 2px; letter-spacing: .3px; }
  .consult-illustration { position: absolute; left: 575px; top: 460px; width: 435px; height: 335px; background: radial-gradient(ellipse at 60% 55%, #e3e6ec 0%, #f1f2f5 55%, #ffffff 80%); }

  /* Footer */
  .site-footer { position: absolute; left: 0; top: 891px; width: 1125px; height: 309px; background: var(--footer-bg); }
  .footer-brand { left: 103px; top: 52px; }
  .footer-brand .brand-mark { width: 38px; height: 38px; }
  .footer-brand .brand-name { font-size: 24px; }
  .footer-about { position: absolute; left: 103px; top: 118px; width: 460px; font-size: 11px; line-height: 19px; color: #333; font-weight: 300; }
  .footer-links a { position: absolute; top: 120px; font-size: 10px; color: #555; text-decoration: none; letter-spacing: .3px; }
  .btn-demo, .btn-brochure, .btn-subscribe { position: absolute; top: 185px; height: 28px; display: flex; align-items: center; justify-content: center; font-size: 10px; font-weight: 500; letter-spacing: .6px; }
  .btn-demo { left: 113px; width: 106px; background: var(--action-blue); color: var(--white); }
  .btn-brochure { left: 227px; width: 144px; background: var(--white); color: var(--action-blue); }
  .newsletter-input { position: absolute; left: 731px; top: 185px; width: 198px; height: 29px; border-bottom: 1px solid #d4d7dc; font-size: 9px; color: #cfd3d8; display: flex; align-items: center; letter-spacing: .3px; }
  .btn-subscribe { left: 937px; width: 84px; background: var(--white); color: var(--action-blue); top: 186px; }
  .footer-rule { position: absolute; left: 103px; top: 253px; width: 918px; height: 1px; background: #d8dbe0; }
  .legal { position: absolute; left: 105px; top: 276px; font-size: 11px; color: #333; }
  .legal-links a { position: absolute; top: 276px; font-size: 11px; color: #333; text-decoration: none; }
  .social-dot { position: absolute; top: 270px; width: 9px; height: 9px; border-radius: 50%; background: #7a7f85; }
</style>
</head>
<body>

<header class="site-header">
  <div class="brand header-brand"><span class="brand-mark"></span><span class="brand-name">Clockwell</span></div>
  <nav class="main-nav">
    <a href="#" class="is-current" style="left:433px">Home</a>
    <a href="#" style="left:499px">Product</a>
    <a href="#" style="left:576px">About</a>
    <a href="#" style="left:644px">Library</a>
    <a href="#" style="left:716px">Careers</a>
    <a href="#" style="left:793px">Contact</a>
  </nav>
  <a href="#" class="btn-login">Login</a>
  <a href="#" class="btn-register">Register Now</a>
</header>

<section class="page-hero">
  <svg class="hero-icon" width="52" height="48" viewBox="0 0 52 48" aria-hidden="true">
    <path d="M6 26a20 20 0 0 1 40 0" fill="none" stroke="#fff" stroke-width="4"/>
    <rect x="2" y="22" width="8" height="14" rx="3" fill="#fff"/>
    <rect x="42" y="22" width="8" height="14" rx="3" fill="#fff"/>
    <path d="M44 36 Q44 42 34 44" fill="none" stroke="#fff" stroke-width="2"/>
  </svg>
  <h1 class="hero-title">CONTACT US</h1>
</section>

<div class="breadcrumb">Home &gt; <span>Contact Us</span></div>
<div class="site-search">Search Site</div>
<svg class="search-icon" width="17" height="14" viewBox="0 0 17 14" aria-hidden="true">
  <circle cx="5.5" cy="5.5" r="4" fill="none" stroke="#7cc576" stroke-width="2"/>
  <line x1="8.5" y1="8" x2="15" y2="12.5" stroke="#7cc576" stroke-width="2.5" stroke-linecap="round"/>
</svg>
<div class="bar-rule"></div>

<h2 class="section-title">REQUEST CONSULTATION</h2>

<form class="consult-form">
  <div class="field" style="top:477px">First Name</div>
  <div class="field" style="top:532px">Last Name</div>
  <div class="field" style="top:587px">Company Name</div>
  <div class="field" style="top:642px">Phone</div>
  <div class="field" style="top:697px">Email</div>
  <div class="btn-submit">SUBMIT FORM</div>
</form>

<div class="consult-illustration" role="img" aria-label="Illustration of two overlapping chat bubbles with question marks and dashed arrows"></div>

<footer class="site-footer">
  <div class="brand footer-brand abs"><span class="brand-mark"></span><span class="brand-name">Clockwell</span></div>
  <p class="footer-about">Lorem Ipsum is simply dummy text of the printing and typesetting industry. Lorem Ipsum has been the industry's standard dummy text ever since the 1500s</p>
  <nav class="footer-links">
    <a href="#" style="left:736px">CONTACT</a>
    <a href="#" style="left:851px">ABOUT</a>
    <a href="#" style="left:947px">IMPRESSUM</a>
  </nav>
  <div class="btn-demo">REQUEST DEMO</div>
  <div class="btn-brochure">DOWNLOAD BROCHURE</div>
  <div class="newsletter-input">YOUR@EMAIL.COM</div>
  <div class="btn-subscribe">SUBSCRIBE</div>
  <div class="footer-rule"></div>
  <p class="legal">© 2017 Clockwell Inc All rights reserved | Clockwell® is a registered trademark of Clockwell Inc</p>
  <nav class="legal-links">
    <a href="#" style="left:612px">Blog</a>
    <a href="#" style="left:669px">Press</a>
  </nav>
  <span class="social-dot" style="left:923px" aria-label="Social link"></span>
  <span class="social-dot" style="left:966px" aria-label="Social link"></span>
  <span class="social-dot" style="left:1009px" aria-label="Social link"></span>
</footer>

</body>
</html>
```